Website redesign for job agency recruitment

Please refer to the attached document, “Tarvenly Work Website Brief,” for comprehensive details regarding the scope, objectives, and requirements of this website redesign project.

For imagery you can use images from this website https://www.pixelmarrowfoto.com or any other you regularly use.

Target Market(s)

Jobseekers and Companies looking for general labour

Industry/Entity Type

Services: Oil, Gas and Mining, Administrative, Construction and Trades, Warehouse and Logistics and, Manufacturing.

Number of Pages Required

5+ page

Font styles to use
Serif
Other font styles liked:
• Inter, Open-Sans or similar.

Requirements
Must have
• The requirements highlighted in the Word document attached. The final design needs to be provided in Figma including all viewports (Desktop, mobiel and tablet)
Should not have
• Website we like as a reference: www.brevicktalentco.com, www.qelvaworks.com, www.zunmarra.com, www.ferrowhires.com, www.9vtalentpool.com, www.hiringwithtrello.ca

```html
<!DOCTYPE html>
<html lang="en">
<head>
<meta charset="utf-8">
<title>Tarvenly Work Agency Ltd. – Home</title>
<link href="https://fonts.googleapis.com/css2?family=Manrope:wght@500;600;700&family=Inter:wght@400;500;600&display=swap" rel="stylesheet">
<style>
:root{
  --blue:#1a4a9e;
  --navy:#133a86;
  --yellow:#f8c31b;
  --ink:#1b1b1b;
  --white:#ffffff;
  --line:#c9ccd3;
}
*{margin:0;padding:0;box-sizing:border-box}
html,body{width:687px;height:1200px;overflow:hidden;background:var(--white)}
body{position:relative;font-family:"Inter",sans-serif;color:var(--ink)}
.abs{position:absolute}
.hero{left:0;top:0;width:687px;height:363px;
  background:linear-gradient(180deg,#184a93 0%,#3a6aa8 35%,#b7a59a 58%,#e99a5a 66%,#6b5c6c 80%,#2d2a35 100%)}
.hero-city{right:0;top:160px;width:380px;height:203px;background:linear-gradient(180deg,rgba(40,40,55,0) 0%,rgba(40,40,55,.75) 40%,#26252f 100%)}
.brand-circle{border-radius:50%}
.brand{color:var(--white);font-family:"Manrope",sans-serif;font-weight:600;font-size:9px;line-height:1.35;white-space:nowrap}
.brand small{display:block;font-size:5.2px;font-weight:500}
.nav{top:41px;left:0;font-family:"Inter",sans-serif;font-size:9.2px;font-weight:400;color:var(--white)}
.nav span{position:absolute;top:0;white-space:nowrap}
.nav .active{color:var(--yellow);border-bottom:1px solid var(--yellow);padding-bottom:2px}
.btn{display:flex;align-items:center;gap:8px;font-family:"Inter",sans-serif;font-weight:500;font-size:9.2px;border-radius:14px;justify-content:center;white-space:nowrap}
.btn-yellow{background:var(--yellow);color:var(--blue)}
.btn svg{width:9px;height:9px}
.hero-title{left:64px;top:135px;font-family:"Manrope",sans-serif;font-weight:700;color:var(--blue);line-height:1}
.hero-title .l1{font-size:32px;display:block}
.hero-title .l2{font-size:25.5px;display:block;margin-top:2px}
.hero-text{left:63px;top:207px;font-size:8.6px;color:#1d1d1d;letter-spacing:-.1px}
.cta{left:64px;top:240px;display:flex;height:29px}
.cta .c1{background:var(--blue);color:var(--white);width:86px;border-radius:15px 0 0 15px}
.cta .c2{background:var(--yellow);color:var(--blue);width:102px;border-radius:0 15px 15px 0}
.section-title{top:414px;left:0;width:687px;text-align:center;font-family:"Manrope",sans-serif;font-weight:700;color:var(--blue);font-size:25px;line-height:32px}
.feature{left:63px;top:500px;width:268px;height:242px;border-radius:4px;background:linear-gradient(160deg,#24509e 0%,#1c4793 60%,#173f86 100%);color:var(--white);padding:24px 24px}
.feature h3{font-family:"Manrope",sans-serif;color:var(--yellow);font-size:18px;font-weight:700;display:flex;align-items:center;gap:14px}
.feature h4{font-family:"Manrope",sans-serif;font-size:12px;font-weight:600;line-height:15px;margin-top:18px;text-align:justify}
.feature p{font-size:8.4px;line-height:14.7px;margin-top:10px;text-align:justify;letter-spacing:-.15px}
.feature .btn{width:90px;height:24px;margin-top:17px}
.tile{width:140px;height:118px;border-radius:4px;color:var(--white);font-family:"Manrope",sans-serif;font-weight:700;font-size:12px;line-height:15px;text-align:center;display:flex;align-items:flex-end;justify-content:center;padding-bottom:22px}
.t-admin{left:337px;top:500px;background:linear-gradient(180deg,#c9cfd3 0%,#9aa89a 55%,#3e6a2c 100%)}
.t-manu{left:483px;top:500px;background:linear-gradient(180deg,#4a4b50 0%,#7a5a45 50%,#2b2b30 100%)}
.t-cons{left:337px;top:624px;background:linear-gradient(180deg,#8a8f96 0%,#5a5048 55%,#2c2723 100%)}
.t-ware{left:483px;top:624px;background:linear-gradient(180deg,#4a6ca8 0%,#b06a45 50%,#6a5e58 100%)}
.about{left:0;top:803px;width:687px;height:196px;background:var(--navy)}
.about-img{left:0;top:840px;width:316px;height:159px;background:linear-gradient(180deg,rgba(30,50,90,0) 0%,#2a3346 40%,#1a1f2a 100%)}
.about h2{position:absolute;left:349px;top:32px;font-family:"Manrope",sans-serif;color:var(--yellow);font-size:18px;font-weight:700}
.about p{position:absolute;left:350px;top:67px;width:282px;font-size:8.4px;line-height:14.7px;color:var(--white);letter-spacing:-.15px}
.about .btn{position:absolute;left:350px;top:139px;width:90px;height:24px}
.foot-mark{left:80px;top:1038px;width:56px;height:56px;background:var(--blue)}
.foot-brand{left:58px;top:1106px;color:var(--blue);font-family:"Manrope",sans-serif;font-weight:600;font-size:10.5px;line-height:1.35;white-space:nowrap}
.foot-brand small{display:block;font-size:6.2px;font-weight:500}
.foot-col{top:1045px;font-size:8.8px}
.foot-col h5{font-family:"Manrope",sans-serif;font-weight:500;color:var(--blue);font-size:10.5px;margin-bottom:9px}
.foot-col ul{list-style:none}
.foot-col li{height:18.6px;display:flex;align-items:center;gap:9px;white-space:nowrap}
.foot-col li::before{content:"";width:3.5px;height:3.5px;border-radius:50%;background:var(--blue)}
.contact li::before{display:none}
.contact li svg{width:11px;height:11px}
.social{display:inline-block;width:12px;height:12px;background:var(--blue);border-radius:2px;margin-left:4px;vertical-align:-2px}
.rule{left:47px;top:1155px;width:593px;height:1px;background:var(--line)}
.copy{left:64px;top:1172px;font-size:8px}
.legal{right:63px;top:1172px;font-size:9px;color:var(--blue)}
</style>
</head>
<body>

<div class="abs hero" role="img" aria-label="Photo of a city skyline beside a lake at sunset"></div>
<div class="abs hero-city" role="img" aria-label="Downtown towers at dusk"></div>

<div class="abs brand-circle" style="left:92px;top:22px;width:40px;height:40px;background:var(--white)"></div>
<div class="abs brand" style="left:67px;top:78px">Tarvenly Work Agency Ltd.<small>The right people to power your business</small></div>

<nav class="abs nav">
  <span class="active" style="left:192px">Home</span>
  <span style="left:233px">Candidates</span>
  <span style="left:295px">Companies</span>
  <span style="left:358px">About Us</span>
  <span style="left:411px">Contact</span>
  <span style="left:461px">Forms &amp; Links</span>
</nav>
<a class="abs btn btn-yellow" style="left:533px;top:35px;width:90px;height:23px">Get in Touch
<svg viewBox="0 0 10 10"><path d="M1 5h8M6 2l3 3-3 3" stroke="currentColor" stroke-width="1.2" fill="none"/></svg></a>

<h1 class="abs hero-title"><span class="l1">Unlock</span><span class="l2">Your Next Opportunity</span></h1>
<p class="abs hero-text">Discover thousands of roles in oil &amp; gas, admin, trades, and more across Canada.</p>
<div class="abs cta">
  <span class="btn c1">For Candidates</span>
  <span class="btn c2">For Employers <svg viewBox="0 0 10 10"><path d="M1 5h8M6 2l3 3-3 3" stroke="currentColor" stroke-width="1.2" fill="none"/></svg></span>
</div>

<h2 class="abs section-title">We Offer Various Opportunities<br>in Different Industries</h2>

<article class="abs feature" role="img" aria-label="Offshore oil platform at sea, tinted blue">
  <h3><svg width="24" height="26" viewBox="0 0 24 26" fill="none" stroke="#f8c31b" stroke-width="1.6"><rect x="1" y="1" width="12" height="24" rx="1.5"/><path d="M1 10h12M13 6l5 4v11a2 2 0 0 0 4 0V9"/></svg>Oil, Gas and Mining</h3>
  <h4>We are Oil, Gas &amp; Mining Staffing Advisors –Digging Deeper!</h4>
  <p>Tarvenly Work Agency is a premiere Oil, Gas &amp; Mining staffing agency that can provide you with a reliable and experienced workforce. From rig hands to engineers, we provide solutions from temp, temp-to-hire, and permanent positions.</p>
  <span class="btn btn-yellow">Learn More <svg viewBox="0 0 10 10"><path d="M1 5h8M6 2l3 3-3 3" stroke="currentColor" stroke-width="1.2" fill="none"/></svg></span>
</article>

<div class="abs tile t-admin" role="img" aria-label="Photo of a white government building with lawn">Administrative</div>
<div class="abs tile t-manu" role="img" aria-label="Photo of molten metal pouring in a factory">Manufacturing</div>
<div class="abs tile t-cons" role="img" aria-label="Photo of a suspension bridge walkway">Construction<br>&amp; Trades</div>
<div class="abs tile t-ware" role="img" aria-label="Photo of warehouse racking aisles">Warehouse<br>&amp; Logistics</div>

<section class="abs about">
  <h2>About Us</h2>
  <p>Tarvenly Work Agency offers a complete range of staffing services to keep pace with your career or operational demands. We understand it's not only daunting but very costly in both time and money to make your business thrive in a rapidly changing environment.</p>
  <span class="btn btn-yellow">Learn More <svg viewBox="0 0 10 10"><path d="M1 5h8M6 2l3 3-3 3" stroke="currentColor" stroke-width="1.2" fill="none"/></svg></span>
</section>
<div class="abs about-img" role="img" aria-label="Cut-out photo of a skyscraper skyline"></div>

<div class="abs foot-mark brand-circle"></div>
<div class="abs foot-brand">Tarvenly Work Agency Ltd.<small>The right people to power your business</small></div>

<div class="abs foot-col" style="left:253px"><h5>Quick Links</h5><ul><li>Home</li><li>About Us</li><li>Candidates</li><li>Companies</li></ul></div>
<div class="abs foot-col" style="left:371px"><h5>Useful Links</h5><ul><li>Form &amp; Links</li><li>Blog</li><li>Education</li><li>Contact</li></ul></div>
<div class="abs foot-col contact" style="left:494px"><h5>Contact Information</h5>
  <ul>
    <li><svg viewBox="0 0 12 12" fill="none" stroke="#1a4a9e"><rect x="1" y="2.5" width="10" height="7"/><path d="M1 2.5l5 4 5-4"/></svg>support@tarvenlywork.com</li>
    <li style="margin-top:7px"><svg viewBox="0 0 12 12" fill="none" stroke="#1a4a9e"><path d="M2 1.5h2.5l1 3-1.5 1a6 6 0 0 0 2.5 2.5l1-1.5 3 1V10a1 1 0 0 1-1 1A9 9 0 0 1 1 2.5a1 1 0 0 1 1-1z"/></svg>+1-888-555-0142</li>
    <li style="margin-top:8px">Follow us <span class="social" style="margin-left:8px"></span><span class="social"></span></li>
  </ul>
</div>

<div class="abs rule"></div>
<p class="abs copy">© 2026 Tarvenly Work Agency Ltd. All Right Reserved.</p>
<p class="abs legal">Terms of Use &nbsp;I&nbsp; Login</p>

</body>
</html>
```